Flyer für Immobilienmakler
Zielgruppe
Wir, die Kessler Immobilien GmbH, vermitteln Häuser, Wohnungen und Grundstücke, unsere Zielgruppe sind Verkäufer und Kaufinteressenten aus der Region, Immobilien zur Vermittlung gesucht
Aufgabenstellung
Unverbindliche Ersteinschätzung, Ansprechpartner vor Ort, regionale Marktkenntnis. Max. Din A 5, Immobilien zur Vermittlung gesucht.
- Flyer nur zur Immobilienvermittlung

```html
<!DOCTYPE html>
<html lang="de">
<head>
<meta charset="utf-8">
<title>Kessler Immobilien GmbH – Flyer Immobilienvermittlung</title>
<link rel="stylesheet" href="https://fonts.googleapis.com/css2?family=Barlow+Semi+Condensed:wght@500;600&family=Inter:wght@400&family=Catamaran:wght@300;400;700&display=swap">
<style>
  :root {
    --page-bg: #d3d3d3;
    --paper: #ffffff;
    --ink: #2b2b2b;
    --ink-soft: #4a4a4a;
    --purple: #6b52a6;
    --purple-dark: #55407f;
    --purple-text: #ddd5f0;
    --green: #1a9a78;
    --arrow: #3a8fc0;
    --band: #2a2a2a;
    --photo-top: #6e6c63;
    --photo-mid: #4c4a40;
    --photo-low: #2e2e28;
  }
  * { box-sizing: border-box; margin: 0; padding: 0; }
  html, body { width: 1200px; height: 1200px; overflow: hidden; }
  body { background: var(--page-bg); font-family: "Inter", sans-serif; }

  .flyer {
    position: absolute; left: 218px; top: 60px;
    width: 764px; height: 1080px;
    background: var(--paper); overflow: hidden;
  }
  .hero-photo {
    position: absolute; left: 0; top: 0; width: 764px; height: 633px;
    background: linear-gradient(170deg, var(--photo-top) 0%, #5d5a50 35%, var(--photo-mid) 60%, var(--photo-low) 100%);
  }
  .hero-photo::after {
    content: ""; position: absolute; inset: 0;
    background: linear-gradient(90deg, rgba(20,20,18,.55) 0%, rgba(20,20,18,.2) 70%, rgba(20,20,18,0) 100%);
  }
  .logo-box {
    position: absolute; left: 49px; top: 0; width: 246px; height: 119px;
    background: var(--paper); border-radius: 0 0 9px 9px;
    display: flex; align-items: center; justify-content: center;
  }
  .logo-name {
    font-family: "Barlow Semi Condensed", sans-serif; font-weight: 600;
    font-size: 19px; color: var(--purple-dark); letter-spacing: .02em;
  }
  .hero-text { position: absolute; left: 42px; top: 263px; color: #fff; }
  .headline {
    font-family: "Barlow Semi Condensed", sans-serif; font-weight: 600;
    font-size: 40px; line-height: 45px; letter-spacing: .045em; text-transform: uppercase;
  }
  .subhead {
    margin-top: 29px;
    font-family: "Barlow Semi Condensed", sans-serif; font-weight: 600;
    font-size: 20px; line-height: 24px; text-transform: uppercase;
  }
  .intro { width: 330px; margin-top: 9px; font-size: 14.3px; line-height: 18px; color: #ececec; }
  .intro p + p { margin-top: 9px; }

  .services { position: absolute; left: 0; top: 633px; width: 390px; }
  .services-title {
    position: absolute; left: 44px; top: 38px; white-space: nowrap;
    font-family: "Barlow Semi Condensed", sans-serif; font-weight: 600;
    font-size: 20px; color: var(--ink); text-transform: uppercase;
  }
  .service { position: absolute; left: 44px; width: 322px; }
  .service::before {
    content: ""; position: absolute; left: -44px; top: 0; width: 7px; height: 59px; background: var(--green);
  }
  .service h3 {
    font-family: "Barlow Semi Condensed", sans-serif; font-weight: 600;
    font-size: 16px; color: var(--ink); text-transform: uppercase; line-height: 20px;
  }
  .service p { margin-top: 3px; font-size: 14.3px; line-height: 18px; color: var(--ink-soft); }

  .bottom-band { position: absolute; left: 0; top: 1055px; width: 764px; height: 25px; background: var(--band); }

  .side-panel { position: absolute; left: 390px; top: 515px; width: 347px; height: 565px; }
  .panel-info { height: 399px; background: var(--purple); padding: 28px 29px 0; }
  .panel-contact { height: 166px; background: var(--purple-dark); padding: 23px 38px 0; color: #fff; }
  .panel-title {
    font-family: "Barlow Semi Condensed", sans-serif; font-weight: 600;
    font-size: 20px; line-height: 23.5px; color: #fff; text-transform: uppercase;
  }
  .panel-title.second { margin-top: 31px; }
  .panel-lead { font-family: "Catamaran", sans-serif; font-weight: 300; font-size: 15px; color: var(--purple-text); margin-top: 4px; }
  .arrow-list { list-style: none; margin-top: 3px; }
  .arrow-list li {
    position: relative; padding-left: 30px; margin-bottom: 5px;
    font-family: "Catamaran", sans-serif; font-weight: 300; font-size: 15px; line-height: 18px; color: var(--purple-text);
  }
  .arrow-list svg { position: absolute; left: 9px; top: 4px; width: 12px; height: 10px; }
  .contact-label, .contact-company {
    font-family: "Barlow Semi Condensed", sans-serif; font-weight: 600; font-size: 16px; text-transform: uppercase;
  }
  .contact-company { margin-top: 19px; line-height: 18px; }
  .contact-line { font-family: "Catamaran", sans-serif; font-weight: 400; font-size: 15px; line-height: 20px; color: #ece6f7; }
  .contact-line b { font-weight: 700; color: #fff; }
  .contact-gap { margin-top: 10px; }
</style>
</head>
<body>
<svg width="0" height="0" style="position:absolute">
  <symbol id="arrow" viewBox="0 0 12 10"><path d="M1 5h9M6 1l4 4-4 4" fill="none" stroke="#3a8fc0" stroke-width="2"/></symbol>
</svg>

<main class="flyer">
  <div class="hero-photo" role="img" aria-label="Luftaufnahme einer Wohnsiedlung mit Einfamilienhäusern, Straßen und Gärten"></div>

  <div class="logo-box"><span class="logo-name">Kessler Immobilien GmbH</span></div>

  <header class="hero-text">
    <h1 class="headline">Ihr regionaler<br>Partner für Immobilien<br>&amp; Vermittlung</h1>
    <h2 class="subhead">Kompetente Immobilienvermittlung<br>vor Ort</h2>
    <div class="intro">
      <p>Die Kessler Immobilien GmbH mit Sitz in Auenfeld ist Ihr zuverlässiger Ansprechpartner für den Verkauf und Kauf von Immobilien.</p>
      <p>Mit fundierter regionaler Marktkenntnis und persönlicher Betreuung unterstützen wir Verkäufer und Kaufinteressenten.</p>
    </div>
  </header>

  <section class="services">
    <h2 class="services-title">Unsere Leistungen</h2>
    <div class="service" style="top:84px">
      <h3>Kostenlose Ersteinschätzung</h3>
      <p>Was ist Ihre Immobilie wert? Wir erstellen Ihnen eine kostenlose und unverbindliche Ersteinschätzung auf Basis aktueller Marktdaten.</p>
    </div>
    <div class="service" style="top:203px">
      <h3>Verkauf Ihrer Immobilie</h3>
      <p>Von der Vermarktung bis zum Notartermin – wir vermitteln Ihr Haus, Ihre Wohnung oder Ihr Grundstück zuverlässig.</p>
    </div>
    <div class="service" style="top:303px">
      <h3>Für Kaufinteressenten</h3>
      <p>Sie suchen ein neues Zuhause? Wir beraten Sie persönlich und finden passende Häuser, Wohnungen und Grundstücke.</p>
    </div>
  </section>

  <div class="bottom-band"></div>

  <aside class="side-panel">
    <div class="panel-info">
      <h2 class="panel-title">Warum Kessler Immobilien?</h2>
      <ul class="arrow-list">
        <li><svg><use href="#arrow"/></svg>Persönlicher Ansprechpartner vor Ort</li>
        <li><svg><use href="#arrow"/></svg>Umfassende regionale Marktkenntnis</li>
        <li><svg><use href="#arrow"/></svg>Kostenlose und unverbindliche Ersteinschätzung</li>
        <li><svg><use href="#arrow"/></svg>Zuverlässiger Partner für Verkäufer und Kaufinteressenten</li>
      </ul>
      <h2 class="panel-title second">Immobilien zur Vermittlung<br>gesucht</h2>
      <p class="panel-lead">Wir sind laufend auf der Suche nach:</p>
      <ul class="arrow-list">
        <li><svg><use href="#arrow"/></svg>Häusern</li>
        <li><svg><use href="#arrow"/></svg>Wohnungen</li>
        <li><svg><use href="#arrow"/></svg>Grundstücken</li>
        <li><svg><use href="#arrow"/></svg>zum Verkauf in der Region.</li>
      </ul>
    </div>
    <div class="panel-contact">
      <div class="contact-label">Kontakt</div>
      <div class="contact-company">Kessler Immobilien GmbH</div>
      <div class="contact-line">Lindenweg 7 84399 Auenfeld</div>
      <div class="contact-line contact-gap"><b>T</b>: +49 85 12 345670-0</div>
      <div class="contact-line"><b>E</b>: immobilien.kessler@kessler-auen.de</div>
    </div>
  </aside>
</main>
</body>
</html>
```